Business card design for holistic health care clinic

We need a double-sided business card design for our holistic health care clinic that integrates our logo design and also its color scheme. My business is called Valmira. It is an integrative medicine clinic. You have already done the logo for me. Please ensure an elegant and upscale design that is not cluttered, but still has all the necessary information (please see below for details).

Target Market(s)

Wellness, fitness, rehabilitation for educated, well-traveled open-minded clients who are focused on natural, organic, balanced and preventive healthcare and lifestyle.

Industry/Entity Type

Medical

Contact Information for Business Card

Modern, clean.

Number of Pages Required

1 page

Font styles to use
Serif
Sans Serif

Colors

Designer to choose colors to be used in the design.

Requirements
Must have
• Logo on one side, all other information on the other side.
• Other information should include:
• Tobias Wrenfeld - DOE, CPT, LMT
• 4100 East Marrow Drive
• Austin, TX 78119
• 512 555 0148
• 818 555 0192
• info@ValmiraHealth.example
• t.wrenfeld@ValmiraHealth.example
Nice to have
• Darker background on front - but not totally black - shaded/dark gray.

```html
<!DOCTYPE html>
<html lang="en">
<head>
<meta charset="utf-8">
<title>Valmira Business Card</title>
<link href="https://fonts.googleapis.com/css2?family=Roboto:ital,wght@0,400;0,500;0,700;1,500&display=swap" rel="stylesheet">
<style>
  :root {
    --page: #ece8e1;
    --card-dark: #2a2a2a;
    --card-dark-edge: #1f1f1f;
    --brand-blue: #1a8fd0;
    --back-blue: #0b92d1;
    --back-blue-light: #2aa0d8;
    --ink: #222222;
    --white: #ffffff;
    --soft-white: #e9e9e9;
  }
  * { margin: 0; padding: 0; box-sizing: border-box; }
  html, body {
    width: 1200px; height: 960px; overflow: hidden;
    background: var(--page);
    font-family: "Roboto", Arial, sans-serif;
  }
  .canvas { position: relative; width: 1200px; height: 960px; }

  .card { position: absolute; width: 600px; height: 343px; overflow: hidden; }

  /* Front */
  .card-front {
    left: 314px; top: 113px;
    background: radial-gradient(ellipse at 50% 40%, var(--card-dark) 0%, var(--card-dark-edge) 100%);
  }
  .accent-bar { position: absolute; left: 116px; width: 373px; height: 6px; background: var(--brand-blue); }
  .accent-bar.top { top: 0; }
  .accent-bar.bottom { bottom: 0; }

  .brand-front { position: absolute; left: 0; top: 90px; width: 600px; text-align: center; }
  .brand-name {
    font-weight: 700; font-size: 50px; line-height: 1; letter-spacing: 1px;
    color: var(--brand-blue);
  }
  .brand-line {
    margin-top: 6px; font-weight: 500; font-size: 16px; color: var(--brand-blue);
  }

  .person {
    position: absolute; right: 321px; top: 210px; text-align: right;
    padding-right: 13px;
  }
  .person::after {
    content: ""; position: absolute; right: 0; top: 3px; width: 4px; height: 34px;
    background: var(--brand-blue);
  }
  .person-name { font-weight: 500; font-size: 20px; color: var(--brand-blue); line-height: 1.1; }
  .person-creds { font-weight: 500; font-size: 11px; color: var(--brand-blue); margin-top: 2px; }

  .address {
    position: absolute; right: 321px; top: 253px; text-align: right;
    font-size: 15px; line-height: 18px; color: var(--soft-white);
  }

  .contact { position: absolute; left: 315px; top: 207px; font-size: 15px; line-height: 18px; color: var(--soft-white); }
  .contact .label { color: var(--brand-blue); font-weight: 700; margin-right: 4px; }
  .contact .web { margin-top: 10px; }

  /* Back */
  .card-back { left: 311px; top: 471px; background: var(--back-blue); }
  .back-decoration {
    position: absolute; left: -70px; top: 30px; width: 330px; height: 330px;
    border-radius: 50%; background: var(--back-blue-light); opacity: 0.55;
  }
  .brand-back { position: absolute; left: 358px; top: 228px; }
  .brand-back .brand-name { font-size: 40px; color: var(--ink); letter-spacing: 0.5px; }
  .brand-back .brand-line { margin-top: 4px; font-size: 13px; color: var(--ink); }
  .tagline {
    margin-top: 6px; font-style: italic; font-weight: 500; font-size: 15px; color: var(--white);
  }
</style>
</head>
<body>
<main class="canvas">
  <section class="card card-front" aria-label="Card front">
    <div class="accent-bar top"></div>
    <div class="brand-front">
      <div class="brand-name">VALMIRA</div>
      <div class="brand-line">Integrative Holistic Medicine</div>
    </div>

    <div class="person">
      <div class="person-name">TOBIAS WRENFELD</div>
      <div class="person-creds">DOE, CPT, LMT</div>
    </div>
    <div class="address">
      <div>4100 East Marrow Drive</div>
      <div>Austin, TX 78119</div>
    </div>

    <div class="contact">
      <div><span class="label">P:</span>512 555 0148</div>
      <div><span class="label">C:</span>818 555 0192</div>
      <div class="web">t.wrenfeld@ValmiraHealth.example</div>
      <div>www.ValmiraHealth.example</div>
    </div>
    <div class="accent-bar bottom"></div>
  </section>

  <section class="card card-back" aria-label="Card back">
    <div class="back-decoration"></div>
    <div class="brand-back">
      <div class="brand-name">VALMIRA</div>
      <div class="brand-line">Integrative Holistic Medicine</div>
      <div class="tagline">helping the body help itself</div>
    </div>
  </section>
</main>
</body>
</html>
```